Quorvane Capital LLC

Need Professional Business cards for New Investment Fund

Target Market(s)

High Quality investors

Industry/Entity Type

Financial

Contact Information for Business Card

Phone Number +1 555 284 6190
Name Lukas Varenko
Title Fund Manager
email lv@FundQuorvane.com
Website www.FundQuorvane.com

Colors

Designer to choose colors to be used in the design.

Requirements
Must have
• Must have our Logo and all of the above. Must be made so lettering and loge can be raised

```html
<!DOCTYPE html>
<html lang="en">
<head>
<meta charset="UTF-8">
<title>Quorvane Capital LLC – Business Card</title>
<link rel="stylesheet" href="https://fonts.googleapis.com/css2?family=Montserrat:wght@600;700&family=Raleway:wght@400;500&display=swap">
<style>
  :root {
    --canvas: #2b2b2b;
    --card-dark: #434e42;
    --accent: #4fb848;
    --paper: #ffffff;
    --ink: #3a4439;
    --ink-soft: #555d54;
    --logo-text: #ffffff;
  }
  * { margin: 0; padding: 0; box-sizing: border-box; }
  html, body {
    width: 1200px; height: 900px; overflow: hidden;
    background: var(--canvas);
  }
  .canvas {
    position: relative; width: 1200px; height: 900px;
    display: flex; flex-direction: column; align-items: center;
    justify-content: center; gap: 30px;
  }
  .card {
    position: relative; width: 700px; height: 400px; overflow: hidden;
    background: var(--card-dark);
    box-shadow: 0 12px 30px rgba(0,0,0,0.5);
  }

  /* Front face */
  .front .brand {
    position: absolute; left: 0; right: 0; top: 150px;
    display: flex; justify-content: center; align-items: center; gap: 14px;
  }
  .brand-mark { width: 26px; height: 26px; background: var(--accent); flex: none; }
  .brand-name {
    font-family: "Montserrat", sans-serif; font-weight: 600;
    color: var(--logo-text); letter-spacing: 3px; white-space: nowrap;
  }
  .front .brand-name { font-size: 42px; }
  .front .accent-bar {
    position: absolute; left: 250px; bottom: 0;
    width: 260px; height: 10px; background: var(--accent);
  }

  /* Back face */
  .back .brand {
    position: absolute; left: 60px; top: 78px;
    display: flex; align-items: center; gap: 10px;
  }
  .back .brand-mark { width: 18px; height: 18px; }
  .back .brand-name { font-size: 28px; }
  .back .divider {
    position: absolute; left: 0; right: 0; top: 210px;
    height: 2px; background: var(--accent);
  }
  .back .info-panel {
    position: absolute; left: 0; right: 0; bottom: 0; height: 176px;
    background: var(--paper);
  }
  .person { position: absolute; left: 60px; top: 38px; }
  .person-accent {
    position: absolute; left: 0; top: 44px; width: 10px; height: 36px;
    background: var(--accent);
  }
  .person-name {
    font-family: "Montserrat", sans-serif; font-weight: 700;
    font-size: 26px; letter-spacing: 0.5px; color: var(--ink);
    text-transform: uppercase; white-space: nowrap;
  }
  .person-name .first { color: var(--accent); }
  .person-title {
    font-family: "Raleway", sans-serif; font-weight: 400;
    font-size: 18px; color: var(--ink-soft); margin-top: 2px;
  }
  .contacts {
    position: absolute; right: 40px; bottom: 20px;
    list-style: none; text-align: right;
    font-family: "Raleway", sans-serif; font-weight: 500;
    font-size: 19px; color: var(--ink-soft);
  }
  .contacts li {
    display: flex; justify-content: flex-end; align-items: center;
    gap: 14px; line-height: 30px; white-space: nowrap;
  }
  .contacts svg { width: 18px; height: 18px; flex: none; }
</style>
</head>
<body>
<main class="canvas">

  <section class="card front" aria-label="Card front">
    <div class="brand">
      <span class="brand-mark"></span>
      <span class="brand-name">QUORVANE</span>
    </div>
    <div class="accent-bar"></div>
  </section>

  <section class="card back" aria-label="Card back">
    <div class="brand">
      <span class="brand-mark"></span>
      <span class="brand-name">QUORVANE</span>
    </div>
    <div class="divider"></div>

    <div class="info-panel">
      <div class="person-accent"></div>
      <div class="person">
        <h1 class="person-name"><span class="first">Lukas</span> Varenko</h1>
        <p class="person-title">Title Fund Manager</p>
      </div>

      <ul class="contacts">
        <li>+1 555 284 6190
          <svg viewBox="0 0 24 24" aria-hidden="true"><path fill="#4fb848" d="M6.6 10.8a15.1 15.1 0 0 0 6.6 6.6l2.2-2.2c.3-.3.7-.4 1-.2 1.1.4 2.3.6 3.6.6.6 0 1 .4 1 1V20c0 .6-.4 1-1 1A17 17 0 0 1 3 4c0-.6.4-1 1-1h3.5c.6 0 1 .4 1 1 0 1.3.2 2.5.6 3.6.1.3 0 .7-.2 1z"/></svg>
        </li>
        <li>lv@FundQuorvane.com
          <svg viewBox="0 0 24 24" aria-hidden="true"><rect x="2.5" y="5" width="19" height="14" rx="1.5" fill="none" stroke="#4fb848" stroke-width="2"/><path d="M3 6l9 7 9-7" fill="none" stroke="#4fb848" stroke-width="2"/></svg>
        </li>
        <li>www.FundQuorvane.com
          <svg viewBox="0 0 24 24" aria-hidden="true"><g fill="none" stroke="#4fb848" stroke-width="1.8"><circle cx="12" cy="12" r="9.5"/><ellipse cx="12" cy="12" rx="4.2" ry="9.5"/><path d="M2.5 12h19M4 7h16M4 17h16"/></g></svg>
        </li>
      </ul>
    </div>
  </section>

</main>
</body>
</html>
```